Need A Standard Musical Download Website

We are looking for a talented designer to create a unique web design for our startup Music website called Vorde Sound.
The website should be responsive and filled with some creative stuffs along with bright colors.

Vorde sound is a website loaded with different types of music and capable of downloading the requested music by its users.
There will be categories of music which would be sorted by the genre. They include RnB, Hip-Hop, Afro pop, Pop, Dancehall and Reggae).

DESIGN STYLE/THEME

Creative, trendy, colorful, unique, and easy to use. You have freedom of selecting which ever color suits you. The design must be energetic and attractive.

NAVIGATION

HOME-MUSIC(RnB, Hip hop, Afro pop, POP, dancehall, Reggae)-ARTISTE-NEWS-LOGIN

PAGES REQUIRED
------------
1)Home Page
2)Music

FONTS
GOOGLE FONTS is strongly recommended.

Designers can get inspiration from https://tunabrook.example

Industry/Entity Type

Startup

```html
<!DOCTYPE html>
<html lang="en">
<head>
<meta charset="utf-8">
<title>Vorde Sound</title>
<link href="https://fonts.googleapis.com/css2?family=Source+Sans+3:wght@300;400;600;700&display=swap" rel="stylesheet">
<style>
  :root {
    --white: #ffffff;
    --ink: #111111;
    --body-text: #3a3a3a;
    --muted-text: #444444;
    --hero-deep: #0a2a3a;
    --hero-teal: #2af0c8;
    --hero-blue: #3f7bff;
    --hero-amber: #ffb23a;
    --hero-pink: #ff4f9a;
    --band-deep: #1e1a3a;
    --band-mid: #5a5fa0;
    --band-warm: #ff9a3a;
    --icon-line: #2a2a2a;
  }
  * { box-sizing: border-box; margin: 0; padding: 0; }
  html, body { width: 996px; height: 1200px; overflow: hidden; background: var(--white); }
  body { font-family: "Source Sans 3", "Source Sans Pro", sans-serif; position: relative; }

  .hero {
    position: absolute; left: 0; top: 0; width: 996px; height: 665px;
    background:
      radial-gradient(ellipse 240px 280px at 340px 300px, rgba(42,240,200,0.85), transparent 70%),
      radial-gradient(ellipse 260px 220px at 540px 330px, rgba(63,123,255,0.75), transparent 70%),
      radial-gradient(ellipse 320px 130px at 850px 270px, rgba(255,178,58,0.7), transparent 70%),
      radial-gradient(ellipse 200px 300px at 50px 300px, rgba(255,178,58,0.6), transparent 70%),
      radial-gradient(ellipse 220px 140px at 230px 80px, rgba(255,79,154,0.55), transparent 70%),
      radial-gradient(ellipse 260px 160px at 860px 480px, rgba(63,123,255,0.5), transparent 70%),
      radial-gradient(ellipse 500px 240px at 480px 640px, rgba(8,50,50,0.85), transparent 80%),
      linear-gradient(180deg, #0f2c52 0%, #0f5560 45%, var(--hero-deep) 100%);
  }
  .site-header { position: absolute; left: 0; top: 0; width: 996px; height: 80px; }
  .brand {
    position: absolute; left: 34px; top: 18px;
    font-size: 27px; font-weight: 600; color: var(--white); letter-spacing: 0.2px;
  }
  .main-nav {
    position: absolute; right: 62px; top: 29px;
    display: flex; gap: 42px;
  }
  .main-nav a {
    font-size: 16px; color: var(--white); line-height: 20px;
    text-decoration: none; letter-spacing: 0.3px;
  }
  .main-nav a.active { border-bottom: 2px solid var(--white); padding: 0 3px 1px; margin: 0 -3px; }
  .hero-title {
    position: absolute; left: 0; width: 996px; top: 160px; text-align: center;
    font-size: 29px; font-weight: 700; line-height: 38px; color: var(--white);
    text-shadow: 0 1px 6px rgba(0,0,0,0.25);
  }
  .cta {
    position: absolute; left: 398px; top: 492px; width: 200px; height: 46px;
    border: 2px solid var(--white); color: var(--white);
    font-size: 16px; letter-spacing: 0.3px; text-align: center; line-height: 42px;
    text-decoration: none;
  }

  .intro {
    position: absolute; left: 80px; top: 688px; width: 846px;
    text-align: center; font-size: 17px; line-height: 21px; color: var(--body-text);
  }

  .features { position: absolute; left: 0; top: 812px; width: 996px; }
  .feature { position: absolute; top: 0; width: 240px; text-align: center; }
  .feature svg { display: block; margin: 0 auto; }
  .feature-title { margin-top: 16px; font-size: 18px; font-weight: 600; color: var(--ink); }
  .feature-text { margin-top: 1px; font-size: 18px; font-weight: 300; color: var(--muted-text); }

  .band {
    position: absolute; left: 0; top: 1053px; width: 996px; height: 147px;
    clip-path: polygon(0 0, 100% 100%, 0 100%);
    background:
      radial-gradient(ellipse 90px 70px at 470px 120px, rgba(255,154,58,0.9), transparent 75%),
      radial-gradient(ellipse 200px 80px at 700px 120px, rgba(150,160,230,0.6), transparent 75%),
      radial-gradient(ellipse 160px 60px at 120px 110px, rgba(255,79,154,0.45), transparent 75%),
      linear-gradient(100deg, var(--band-deep) 0%, var(--band-mid) 55%, var(--band-deep) 100%);
  }
</style>
</head>
<body>
  <section class="hero" role="img" aria-label="Concert crowd photo with raised hands forming a heart under bright stage lights">
    <header class="site-header">
      <div class="brand">VordeSound</div>
      <nav class="main-nav">
        <a class="active" href="#">HOME</a>
        <a href="#">MUSIC</a>
        <a href="#">ARTISTE</a>
        <a href="#">NEWS</a>
        <a href="#">LOGIN</a>
      </nav>
    </header>
    <h1 class="hero-title">All the music you love and<br>all the music you will love</h1>
    <a class="cta" href="#">START MY JOURNEY</a>
  </section>

  <p class="intro">"Lorem ipsum dolor sit amet, consectetur adipiscing elit, sed do eiusmod tempor incididunt ut labore et dolore magna aliqua. Ut enim ad minim veniam, quis nostrud exercitation ullamco laboris nisi ut aliquip ex ea commodo consequat. Duis aute irure dolor in reprehenderit in voluptate velit esse cillum dolore eu fugiat nulla pariatur. Excep-teur sint occaecat cupidatat non proident, sunt in culpa qui officia deserunt mollit anim id est laborum."</p>

  <section class="features">
    <div class="feature" style="left:89px">
      <svg width="88" height="150" viewBox="0 0 88 150" fill="none" stroke="var(--icon-line)" stroke-width="1.3">
        <rect x="1" y="1" width="86" height="148" rx="9"/>
        <rect x="5" y="5" width="78" height="128" rx="6"/>
        <circle cx="44" cy="141" r="5"/>
        <rect x="12" y="42" width="26" height="28" rx="10"/>
        <line x1="44" y1="49" x2="76" y2="49"/><line x1="44" y1="55" x2="76" y2="55"/>
        <line x1="44" y1="61" x2="76" y2="61"/><line x1="44" y1="67" x2="76" y2="67"/>
      </svg>
      <div class="feature-title">Sample Topic</div>
      <div class="feature-text">Some more text below</div>
    </div>
    <div class="feature" style="left:378px">
      <svg width="88" height="150" viewBox="0 0 88 150" fill="none" stroke="var(--icon-line)" stroke-width="1.3">
        <rect x="1" y="1" width="86" height="148" rx="9"/>
        <rect x="5" y="5" width="78" height="128" rx="6"/>
        <circle cx="44" cy="141" r="5"/>
        <rect x="12" y="42" width="26" height="28" rx="10"/>
        <line x1="44" y1="49" x2="76" y2="49"/><line x1="44" y1="55" x2="76" y2="55"/>
        <line x1="44" y1="61" x2="76" y2="61"/><line x1="44" y1="67" x2="76" y2="67"/>
      </svg>
      <div class="feature-title">Sample Topic</div>
      <div class="feature-text">Some more text below</div>
    </div>
    <div class="feature" style="left:666px">
      <svg width="88" height="150" viewBox="0 0 88 150" fill="none" stroke="var(--icon-line)" stroke-width="1.3">
        <rect x="1" y="1" width="86" height="148" rx="9"/>
        <rect x="5" y="5" width="78" height="128" rx="6"/>
        <circle cx="44" cy="141" r="5"/>
        <rect x="12" y="42" width="26" height="28" rx="10"/>
        <line x1="44" y1="49" x2="76" y2="49"/><line x1="44" y1="55" x2="76" y2="55"/>
        <line x1="44" y1="61" x2="76" y2="61"/><line x1="44" y1="67" x2="76" y2="67"/>
      </svg>
      <div class="feature-title">Sample Topic</div>
      <div class="feature-text">Some more text below</div>
    </div>
  </section>

  <div class="band" role="img" aria-label="Festival stage photo with lights and a colourful stage decoration"></div>
</body>
</html>
```